Write a tag line/slogan for A new skin care brand

Amazing tag line wanted for a new skin care brand.
This skin care ranges claim to fame is the use of unique and potent plant extracts sourced from the Mediterranean .
These ingredients are unique to this location and the medicinal properties of these plants dates back thousands of years. With many myths and stories in history about there uses etc.
The local inhabitants to this day use these plants instead of a more science based medicine. For example one of the ingredients is Dittany.
This population has remarkable longevity, health and youth fullness thought to be achieved by consumption and use of these plants.
These antioxidant and rejuvenating extracts are the basis of the skin care line.
This range consists of face, body and hair care products. All products are vegan, dermatologically tested, with no mineral oils, parabens etc.
These products are gender friendly
Will be distributed throughout Australia, Europe and America.
Attached is the loge brand name
Please write your tag line in large text as some of them are so small I don't know what you have said . Thank you
Does not have to have the word Mediterranean in it.

```html
<!DOCTYPE html>
<html lang="en">
<head>
<meta charset="utf-8">
<title>Glowing skin - awakened by the earth</title>
<link rel="stylesheet" href="https://fonts.googleapis.com/css2?family=Cabin:wght@700&display=swap">
<style>
  :root {
    --sky-blue: #00aeef;
    --white: #ffffff;
  }
  html, body {
    margin: 0;
    padding: 0;
    width: 1200px;
    height: 900px;
    overflow: hidden;
    background: var(--sky-blue);
  }
  .tagline-board {
    position: relative;
    width: 1200px;
    height: 900px;
    background: var(--sky-blue);
  }
  .tagline {
    position: absolute;
    left: 104px;
    top: 220px;
    margin: 0;
    font-family: "Cabin", "Trebuchet MS", sans-serif;
    font-weight: 700;
    font-size: 115px;
    line-height: 145px;
    letter-spacing: -0.5px;
    color: var(--white);
  }
  .tagline-line {
    display: block;
    white-space: nowrap;
  }
</style>
</head>
<body>
  <main class="tagline-board">
    <h1 class="tagline">
      <span class="tagline-line">Glowing skin -</span>
      <span class="tagline-line">awakened by</span>
      <span class="tagline-line">the earth</span>
    </h1>
  </main>
</body>
</html>
```